New Brand - Website Design (4 Pages)

We are launching a new brand for electronic cigarettes. We already have logo and packaging done and would like a web design to go with it.

We are interested in the following deliverables:

1) Home Page Design
2) Check Out Design
3) How it Works Page
4) Secondary Template Page Design

Looking for a 60s modern look and something that is consistent with our logo and packaging.

Industry/Entity Type

Electronic

Requirements
Must have
• Consistent with logo and packaging (Use Logo Attached)
White background

Example (Functionality & Design): http://www.moltrafen.co.uk/
Example (Design): http://www.brendolark.com/

We want the design more like brendolark but the functionality the same as moltrafen.

Top Bar: Pale Dunes Kits; Cartridge Refills; How it Works; Contact; My Account; Checkout
Should not have
• Stock List or Search Bar or Newsletter Signup

```html
<!DOCTYPE html>
<html lang="en">
<head>
<meta charset="utf-8">
<title>Pale Dunes – Product</title>
<link rel="stylesheet" href="https://fonts.googleapis.com/css2?family=Jura:wght@300;400;500&family=Source+Sans+3:wght@400;600&display=swap">
<style>
:root{
  --page:#ececec;
  --panel:#252525;
  --sky:#1ea1e0;
  --button:#6fb3d6;
  --tan:#c99b6e;
  --list:#c89a70;
  --ink:#1d1d1d;
  --white:#ffffff;
  --rule:#6a6a6a;
  --slider:#4a4a4a;
  --placeholder-dark:#303030;
  --placeholder-light:#d6d6d6;
}
*{margin:0;padding:0;box-sizing:border-box}
html,body{width:1200px;height:1000px;overflow:hidden}
body{background:var(--page);font-family:"Source Sans 3",sans-serif;color:var(--ink);position:relative}
.abs{position:absolute}
.display{font-family:"Jura",sans-serif;font-weight:300;text-transform:uppercase;line-height:1}

.tip-visual{left:112px;top:0;width:250px;height:90px;background:linear-gradient(135deg,#1a1a1a 0%,#3a3a3a 100%)}
.callout-line{left:140px;top:64px}
.callout-label{left:286px;top:61px;font-family:"Jura",sans-serif;font-size:16px;color:#9a9a9a}
.spec-text{left:652px;top:-2px;width:460px;font-size:15px;line-height:17px;color:#2a2a2a}
.spec-title{left:652px;top:29px;font-family:"Jura",sans-serif;font-weight:400;font-size:22px;line-height:22px;color:#555}
.spec-body{left:652px;top:50px;width:460px;font-size:15px;line-height:17px;color:#2a2a2a}

.btn{display:flex;align-items:center;justify-content:space-between;width:106px;height:24px;padding:0 8px 0 7px;background:var(--button);color:var(--white);font-family:"Source Sans 3",sans-serif;font-weight:600;font-size:12px;letter-spacing:.3px;text-transform:uppercase;text-decoration:none}
.btn svg{width:8px;height:13px}

.product-panel{left:105px;top:154px;width:991px;height:633px;background:var(--panel)}
.product-title{left:140px;top:196px;font-size:42px;line-height:52px;color:var(--white);letter-spacing:1px}
.slider{left:143px;top:323px;width:145px;height:24px;border-radius:12px;background:var(--slider);display:flex;overflow:hidden}
.slider span{flex:1;display:flex;align-items:center;justify-content:center}
.slider span:first-child{background:#5c5c5c}
.pack-visual{left:416px;top:213px;width:242px;height:290px;background:linear-gradient(180deg,var(--placeholder-dark) 0%,#2a2a2a 100%)}
.headline{left:698px;top:206px;font-size:19.5px;line-height:18px;font-weight:400;color:var(--white)}
.headline .accent{color:var(--tan)}
.dotted{border-top:1px dotted var(--rule)}
.rule-a{left:700px;top:247px;width:358px}
.sub-head{left:773px;top:262px;font-size:16px;font-weight:400;color:var(--white)}
.rule-b{left:773px;top:285px;width:187px}
.features{left:776px;top:290px;list-style:none;font-size:12px;line-height:15.2px;color:var(--list)}
.rule-c{left:773px;top:431px;width:187px}
.price{left:795px;top:443px;font-family:"Jura",sans-serif;font-size:21px;color:var(--white)}
.buy{left:779px;top:473px}

.tweet-title{left:143px;top:588px;font-size:47px;color:var(--white)}
.tweet-copy{left:143px;top:638px;font-size:28px;line-height:29px;color:var(--white)}
.tweet-btn{left:143px;top:739px}

.contact-box{left:600px;top:570px;width:496px;height:217px;background:var(--sky)}
.contact-title{left:637px;top:589px;font-size:46px;color:var(--white)}
.contact-mail{left:637px;top:637px;font-family:"Jura",sans-serif;font-weight:300;font-size:28px;color:var(--white)}
.social{left:639px;top:685px;display:flex;gap:9px}
.social span{width:30px;height:30px;border-radius:50%;background:var(--white)}
.contact-btn{left:639px;top:739px}

.warning-visual{left:105px;top:841px;width:107px;height:82px;background:linear-gradient(180deg,#111 0%,#2a2a2a 100%)}
.warning{left:219px;top:837px;width:860px;font-size:18px;line-height:22px;color:var(--ink)}
.legal{left:0;top:950px;width:1200px;text-align:center;font-size:15px;color:var(--ink)}
</style>
</head>
<body>

<section class="specs">
  <div class="abs tip-visual" role="img" aria-label="Black e-cigarette with silicone tip"></div>
  <svg class="abs callout-line" width="140" height="14" viewBox="0 0 140 14"><line x1="0" y1="7" x2="128" y2="7" stroke="#9a9a9a" stroke-width="1.5"/><circle cx="130" cy="7" r="5" fill="#9a9a9a"/></svg>
  <span class="abs callout-label">Silicone Tip</span>
  <p class="abs spec-text">intake for maximized draw and resistance for cigarette feel.</p>
  <h3 class="abs spec-title">Size</h3>
  <p class="abs spec-body">nimbo Premium electronic cigarettes are the same size as a traditional cigarette and fit all Original and Premium e-cigarette starter kits.</p>
  <a class="abs btn" style="left:952px;top:95px" href="#">Find more <svg viewBox="0 0 8 13"><path d="M1 1l6 5.5L1 12" fill="none" stroke="#fff" stroke-width="1.5"/></svg></a>
</section>

<section class="abs product-panel" aria-label="Featured product"></section>
<h2 class="abs display product-title">Pale Dunes<br>Product</h2>
<div class="abs slider">
  <span><svg width="8" height="13" viewBox="0 0 8 13"><path d="M7 1L1 6.5 7 12" fill="none" stroke="#fff" stroke-width="1.5"/></svg></span>
  <span><svg width="8" height="13" viewBox="0 0 8 13"><path d="M1 1l6 5.5L1 12" fill="none" stroke="#fff" stroke-width="1.5"/></svg></span>
</div>
<div class="abs pack-visual" role="img" aria-label="Product pack photo: Pale Dunes cartomiser box"></div>

<h3 class="abs display headline"><span class="accent">Apple Flover</span> now with apple flavor.<br>You definitely attracted</h3>
<div class="abs dotted rule-a"></div>
<h4 class="abs display sub-head">More fresh and soft</h4>
<div class="abs dotted rule-b"></div>
<ul class="abs features">
  <li>Disposable E-Cig, Easy to Use</li>
  <li>MAXILOOP™ Technology</li>
  <li>Real Cigarette Size and Feel</li>
  <li>SOFTBEND TIP™ Soft Filter</li>
  <li>Pale Dunes BLUE at the Tip</li>
  <li>Black White at the Tip</li>
  <li>In Tobacco &amp; Menthol Flavors</li>
  <li>1.8% Nicotine by Volume</li>
  <li>Each King lasts ~160 Puffs</li>
</ul>
<div class="abs dotted rule-c"></div>
<p class="abs price">$ 9.99</p>
<a class="abs btn buy" href="#">Buy now <svg viewBox="0 0 8 13"><path d="M1 1l6 5.5L1 12" fill="none" stroke="#fff" stroke-width="1.5"/></svg></a>

<h2 class="abs display tweet-title">Tweeting</h2>
<p class="abs display tweet-copy">The best whay to make SEO<br>is to combine advertising,<br>bloging nad tweeting</p>
<a class="abs btn tweet-btn" href="#">Find more <svg viewBox="0 0 8 13"><path d="M1 1l6 5.5L1 12" fill="none" stroke="#fff" stroke-width="1.5"/></svg></a>

<section class="abs contact-box" aria-label="Contact"></section>
<h2 class="abs display contact-title">Contact us</h2>
<p class="abs contact-mail">info@tessaplate.com</p>
<div class="abs social" aria-label="Social links"><span></span><span></span><span></span><span></span><span></span></div>
<a class="abs btn contact-btn" href="#">Find more <svg viewBox="0 0 8 13"><path d="M1 1l6 5.5L1 12" fill="none" stroke="#fff" stroke-width="1.5"/></svg></a>

<div class="abs warning-visual" role="img" aria-label="Pale Dunes product card"></div>
<p class="abs warning">WARNING: This product contains nicotine, a chemical known to the state of California to cause birth defects or other reproductive harm. This product has not been approved by the United States Food and Drug Administra&shy;tion. Keep out of reach of children. Refrain from using this product if you are under the legal smoking age in your state. This product is not an aid for smoking cessation.</p>
<p class="abs legal">© 2013 PALE DUNES BY KORVALEN. &nbsp; ALL RIGHTS RESERVED.</p>

</body>
</html>
```